Tradeshow wall graphic featuring exhibitor branding

We are a software company representing the cruise industry. We are at a small trade show booth and need front and back artwork. We would like to include verbage from the attached word document. I have also included some past banners that we have used for reference. plinthwave.com

```html
<!DOCTYPE html>
<html lang="en">
<head>
<meta charset="utf-8">
<title>Plinthwave – Trade Show Wall Graphic</title>
<link href="https://fonts.googleapis.com/css2?family=Bebas+Neue&family=Roboto:wght@400;500;700;900&display=swap" rel="stylesheet">
<style>
  :root {
    --backdrop: #cdcdcd;
    --navy-deep: #0a1f38;
    --navy-band: #0c3658;
    --navy-text: #0b1f3a;
    --accent-blue: #1a9be0;
    --white: #ffffff;
    --sky-top: #3f7fbf;
    --sunset-orange: #f08a4b;
    --sunset-gold: #f7c54a;
    --sea-light: #2a87b8;
    --sea-deep: #0d3a60;
  }
  * { box-sizing: border-box; margin: 0; padding: 0; }
  html, body { width: 882px; height: 1200px; overflow: hidden; background: var(--backdrop); }
  body { position: relative; font-family: "Roboto", Arial, sans-serif; }

  .poster {
    position: absolute; left: 80px; top: 76px; width: 722px; height: 1048px;
    background: var(--navy-deep); overflow: hidden; color: var(--white);
  }
  .hero-photo {
    position: absolute; left: 0; top: 0; width: 100%; height: 698px;
    background:
      linear-gradient(180deg, transparent 0%, transparent 70%, rgba(13,58,96,0.9) 100%),
      linear-gradient(180deg, var(--sky-top) 0%, #6a7fb0 14%, var(--sunset-orange) 32%, var(--sunset-gold) 48%, #f4d27a 51%, var(--sea-light) 52%, var(--sea-deep) 100%);
  }
  .brand-name {
    position: absolute; left: 0; right: 0; top: 46px; text-align: center;
    font-weight: 900; font-size: 70px; line-height: 64px; letter-spacing: 2px; color: var(--white);
  }
  .audience-pill {
    position: absolute; left: 95px; top: 131px; width: 533px; height: 48px;
    background: var(--white); border-radius: 24px; display: flex; align-items: center; justify-content: center;
    font-family: "Bebas Neue", "Oswald", sans-serif; font-size: 27px; color: var(--navy-text); letter-spacing: 0.5px;
  }
  .headline { position: absolute; left: 0; right: 0; text-align: center; font-weight: 700; text-transform: uppercase; }
  .headline-top { top: 580px; font-size: 37px; line-height: 40px; }
  .headline-main { top: 622px; font-size: 46px; line-height: 50px; letter-spacing: 0.5px; }

  .platform-band {
    position: absolute; left: 0; top: 698px; width: 100%; height: 46px; background: var(--navy-band);
    display: flex; align-items: center; justify-content: center; gap: 17px;
    font-weight: 700; font-size: 27px;
  }
  .rule { display: block; width: 35px; height: 1.5px; background: var(--white); }
  .platform-band .rule { margin: 0 0; }

  .summary { position: absolute; left: 0; right: 0; top: 762px; text-align: center; font-size: 16px; font-weight: 500; }

  .feature { position: absolute; display: flex; align-items: center; }
  .feature-icon {
    width: 56px; height: 56px; border-radius: 50%; background: var(--white);
    border: 2px solid var(--accent-blue); display: flex; align-items: center; justify-content: center;
  }
  .feature-icon svg { width: 32px; height: 32px; }
  .feature-label { margin-left: 27px; font-size: 22px; line-height: 25px; font-weight: 400; }
  .feature-a { left: 96px; top: 811px; }
  .feature-b { left: 403px; top: 811px; }
  .feature-c { left: 96px; top: 888px; }
  .feature-d { left: 403px; top: 888px; }
  .feature-b .feature-label, .feature-d .feature-label { margin-left: 20px; }

  .demo-curve { position: absolute; left: 0; bottom: 0; width: 100%; height: 80px; }
  .demo-callout {
    position: absolute; left: 0; right: 0; top: 1004px; display: flex; align-items: center; justify-content: center; gap: 14px;
    color: var(--navy-text); font-weight: 900; font-size: 31px;
  }
  .demo-callout .rule { background: var(--navy-text); width: 34px; }
</style>
</head>
<body>
  <main class="poster">
    <div class="hero-photo" role="img" aria-label="Cruise ship sailing on open sea at sunset under an orange and blue sky"></div>

    <div class="brand-name">PLINTHWAVE</div>
    <div class="audience-pill">Built for Cruise Lines &amp; Shore Excursion Operators</div>

    <h1 class="headline headline-top">Control Cruise Inventory</h1>
    <h2 class="headline headline-main">And Direct Bookings</h2>

    <div class="platform-band">
      <span class="rule"></span><span>SEAMLESSLY ON ONE PLATFORM</span><span class="rule"></span>
    </div>

    <p class="summary">The all-in-one operating system powering cruise-based tour operations</p>

    <div class="feature feature-a">
      <span class="feature-icon">
        <svg viewBox="0 0 32 32" fill="#0b1f3a">
          <circle cx="16" cy="8" r="4"/><path d="M9 19c0-4 3-6 7-6s7 2 7 6z"/>
          <circle cx="7" cy="10" r="2.5" fill="none" stroke="#0b1f3a" stroke-width="1.3"/>
          <circle cx="25" cy="10" r="2.5" fill="none" stroke="#0b1f3a" stroke-width="1.3"/>
          <path d="M8 21l1.2 2.4 2.6.3-1.9 1.8.5 2.6L8 26.9l-2.4 1.2.5-2.6-1.9-1.8 2.6-.3zM16 21l1.2 2.4 2.6.3-1.9 1.8.5 2.6-2.4-1.2-2.4 1.2.5-2.6-1.9-1.8 2.6-.3zM24 21l1.2 2.4 2.6.3-1.9 1.8.5 2.6-2.4-1.2-2.4 1.2.5-2.6-1.9-1.8 2.6-.3z"/>
        </svg>
      </span>
      <span class="feature-label">Maximize<br>Occupancy.</span>
    </div>

    <div class="feature feature-b">
      <span class="feature-icon">
        <svg viewBox="0 0 32 32" fill="none" stroke="#0b1f3a" stroke-width="1.8">
          <rect x="4" y="5" width="9" height="8"/><path d="M4 9h9"/>
          <circle cx="25" cy="8" r="3" fill="#0b1f3a"/><path d="M20 16c0-3 2-4 5-4s5 1 5 4z" fill="#0b1f3a"/>
          <path d="M15 8h4M17 11h-2"/>
          <path d="M3 23l5-3h6l4 2h6l-8 5H9z"/>
        </svg>
      </span>
      <span class="feature-label">Manage<br>Direct Sales.</span>
    </div>

    <div class="feature feature-c">
      <span class="feature-icon">
        <svg viewBox="0 0 32 32" fill="none" stroke="#0b1f3a" stroke-width="2">
          <circle cx="17" cy="18" r="10"/><path d="M17 18l-5-5M4 4l5 5"/>
          <circle cx="17" cy="18" r="1.6" fill="#0b1f3a"/>
        </svg>
      </span>
      <span class="feature-label">Control<br>Cruise Inventory.</span>
    </div>

    <div class="feature feature-d">
      <span class="feature-icon">
        <svg viewBox="0 0 32 32" fill="none" stroke="#0b1f3a" stroke-width="1.8">
          <path d="M11 6l6-3 6 3v7l-6 3-6-3z"/><path d="M11 6l6 3 6-3M17 9v7"/>
          <path d="M25 6l4 4-4 4"/><path d="M3 8h5M3 12h5"/>
          <path d="M3 25l5-3h6l4 2h6l-8 5H9z"/>
        </svg>
      </span>
      <span class="feature-label">Power Daily<br>Dispatch.</span>
    </div>

    <svg class="demo-curve" viewBox="0 0 722 80" preserveAspectRatio="none" aria-hidden="true">
      <path d="M0 54 Q361 -30 722 54 L722 80 L0 80 Z" fill="#ffffff"/>
    </svg>
    <div class="demo-callout">
      <span class="rule"></span><span>LIVE DEMOS AT HARBORLINE</span><span class="rule"></span>
    </div>
  </main>
</body>
</html>
```